Simple, High-Class Web Design Wanted - Motivational Speakers Site

1. Full Brief/Request & Specs outlined on following video -
http://clipvault-demo.com/watch/rTkWmaPzQb

2. Use colours, images as you feel suits objective (we are happy to pay up to US$30 for any good images but must have licence/permission).

3. Layout probably similar to existing site - www.podiumtalentgroup.com.au / http://podiumtalentgroup.com.au/contact.php

4. Must Be Able to Coded for MOBILE-FRIENDLINESS & WordPress friendly Ideal.

5. This is the first, small job of many we/graphic design jobs. If suits, winning designer may be offered all future work direct.

Thanks & look forward to your design. Glen.

Target Market(s)

corporates - high end

Number of Pages Required

2 page

Font styles to use
Sans Serif

Requirements
Must have
• Classy professional look
Nice to have
• all in Video in brief
Should not have
• too many images / new images I haven't approved

```html
<!DOCTYPE html>
<html lang="en">
<head>
<meta charset="utf-8">
<title>Podium Talent Group – Find the Speaker for Your Next Event</title>
<link href="https://fonts.googleapis.com/css2?family=Open+Sans:wght@400;600;700;800&display=swap" rel="stylesheet">
<style>
:root{
  --navy:#12345e;
  --green:#6cb21f;
  --green-dark:#4f8f12;
  --blue-1:#1b5fa8;
  --blue-2:#0d3b73;
  --text:#444b55;
  --muted:#8a9099;
  --rule:#c9d3dd;
  --panel:#f7f9fb;
  --white:#ffffff;
}
*{box-sizing:border-box;margin:0;padding:0}
html,body{width:887px;height:1200px;overflow:hidden;background:var(--white)}
body{font-family:"Open Sans",Arial,sans-serif;color:var(--text);position:relative}
.page-title{position:absolute;top:14px;left:0;width:887px;text-align:center}
.page-title .line-1{font-size:47px;font-weight:800;color:var(--navy);letter-spacing:1px;line-height:52px}
.page-title .line-2{font-size:36px;font-weight:800;color:var(--green);line-height:46px;margin-top:4px;text-align:left;padding-left:126px}
.page-title .line-2 small{font-size:22px;color:var(--navy);font-weight:700;margin-left:10px}
.hero{position:absolute;top:118px;left:14px;width:859px;height:310px;background:linear-gradient(135deg,var(--blue-1),var(--blue-2));overflow:hidden}
.hero-figure{position:absolute;left:10px;top:0;width:112px;height:310px;background:linear-gradient(180deg,#3b4452 0%,#262c35 60%,#1d2229 100%)}
.hero-pitch{position:absolute;left:132px;top:26px;width:138px;color:var(--white);font-weight:800;font-size:15px;line-height:19px;text-transform:uppercase}
.hero-pitch .lead{font-size:11px;line-height:15px;font-weight:700;display:block}
.hero-pitch .big{display:block;font-size:15px;line-height:19px;letter-spacing:-.2px}
.hero-pitch .soft{display:block;font-size:10.5px;line-height:15px;font-weight:700;margin-top:4px}
.hero-pitch .accent{color:var(--green);font-size:24px;line-height:26px;margin-top:12px;display:block}
.video{position:absolute;left:276px;top:12px;width:570px;height:288px;background:linear-gradient(160deg,#8fa9b8,#50697a);border:3px solid var(--white)}
.video .play{position:absolute;left:258px;top:104px}
.video .controls{position:absolute;left:0;bottom:0;width:100%;height:28px;background:#1d1f22}
.cta{position:absolute;display:flex;align-items:center;justify-content:center;background:var(--green);color:var(--white);font-weight:700;border:1px solid var(--green-dark)}
.cta-main{top:440px;left:293px;width:300px;height:34px;font-size:13px}
.intro{position:absolute;top:500px;left:40px;width:807px;font-size:10.5px;line-height:17px}
.intro p{margin-bottom:10px}
.intro ul{list-style:none;margin:4px 0 10px 8px}
.intro li{padding-left:14px;position:relative;font-weight:600}
.intro li::before{content:"";position:absolute;left:0;top:7px;width:5px;height:5px;background:var(--navy)}
.intro a{color:var(--blue-1)}
.contact-row{position:absolute;left:0;width:887px;display:flex;justify-content:center;align-items:center;gap:26px;font-size:10.5px}
.contact-row .cta{position:static;width:230px;height:28px;font-size:11px}
.contact-row .item{display:flex;align-items:center;gap:6px;color:var(--blue-1)}
.contact-row .item.phone{color:var(--navy);font-weight:700}
.row-1{top:718px}
.notice{position:absolute;top:770px;left:40px;width:807px;height:360px;border:1px solid var(--rule);background:var(--panel)}
.notice h2{text-align:center;color:var(--navy);font-size:22px;font-weight:800;margin-top:16px;padding-bottom:14px;border-bottom:1px solid var(--rule)}
.notice ul{list-style:none;margin:24px 30px 0;font-size:10.5px;line-height:16px}
.notice li{display:flex;gap:10px;margin-bottom:16px}
.notice li svg{flex:none;margin-top:2px}
.row-2{top:1060px}
.footer{position:absolute;top:1170px;left:0;width:887px;text-align:center;font-size:9px;color:var(--muted)}
</style>
</head>
<body>
<header class="page-title">
  <div class="line-1">FIND THE SPEAKER FOR YOUR</div>
  <div class="line-2">NEXT EVENT HERE ... <small>FREE INDUSTRY SERVICE</small></div>
</header>

<section class="hero">
  <div class="hero-figure" role="img" aria-label="Photo of a speaker in a dark business suit"></div>
  <div class="hero-pitch">
    <span class="lead">Looking for top</span>
    <span class="big">Motivational</span>
    <span class="big">or guest</span>
    <span class="big">speaker, MC,</span>
    <span class="soft">or industry expert to 'wow' your next event ?</span>
    <span class="accent">Find them here</span>
  </div>
  <div class="video" role="img" aria-label="Introductory video still of a presenter speaking to camera">
    <svg class="play" width="48" height="48" viewBox="0 0 48 48"><circle cx="24" cy="24" r="23" fill="rgba(255,255,255,.85)"/><path d="M19 14 L35 24 L19 34Z" fill="#1d1f22"/></svg>
    <div class="controls">
      <svg width="564" height="28" viewBox="0 0 564 28"><path d="M10 8 L20 14 L10 20Z" fill="#fff"/><rect x="32" y="12" width="440" height="4" fill="#555"/><rect x="32" y="12" width="60" height="4" fill="#6cb21f"/><rect x="490" y="9" width="14" height="10" fill="#ccc"/><rect x="520" y="9" width="30" height="10" fill="#ccc"/></svg>
    </div>
  </div>
</section>

<a class="cta cta-main">I want to make our Event a Great Success</a>

<section class="intro">
  <p>Podium Talent Group is a free industry service designed to help people looking for speakers save precious time and frustration in finding the most committed speaker for their needs.</p>
  <p>Suggestions are given by Podium conference speaker Glen, who has presented around the country for many years and is familiar with many of our top professional speakers, MCs and leading experts.</p>
  <p>If you would like a hand finding some great speaker options, simply send us the details of your event and the type of presenter you are already after, e.g.</p>
  <ul>
    <li>Type/Style – Motivational, Entertaining, Keynote/Workshop, MC etc</li>
    <li>Topic/Area – Team Building, Leadership, Inspiration, Health/Life Balance etc</li>
    <li>Approximate Budget – $2000, $4000, $7000, $10000+ etc</li>
    <li>Location – Sydney, Melbourne, Brisbane, Perth, Adelaide, Canberra etc</li>
  </ul>
  <p>And before we start, we will be happy to send you some speaker suggestions. Glen will shortlist options for you fast. <a>Enquire here</a></p>
</section>

<div class="contact-row row-1">
  <a class="cta">Quick Online Contact Form</a>
  <span class="item"><svg width="16" height="12" viewBox="0 0 16 12"><rect x=".5" y=".5" width="15" height="11" fill="none" stroke="#6cb21f"/><path d="M1 1 L8 7 L15 1" fill="none" stroke="#6cb21f"/></svg>suggestions@podiumtalentgroup.com.au</span>
  <span class="item phone"><svg width="12" height="14" viewBox="0 0 12 14"><path d="M2 1 L5 1 L5 4 L3.5 5 Q5 9 8 10.5 L9 9 L12 9 L12 12 Q6 14 1 5 Z" fill="#6cb21f"/></svg>1300 555 482</span>
</div>

<section class="notice">
  <h2>PLEASE NOTE</h2>
  <ul>
    <li><svg width="14" height="12" viewBox="0 0 14 12"><path d="M1 6 L5 10 L13 1" fill="none" stroke="#6cb21f" stroke-width="2.5"/></svg>Any information you provide will only ever be used to help with your specific enquiry.</li>
    <li><svg width="14" height="12" viewBox="0 0 14 12"><path d="M1 6 L5 10 L13 1" fill="none" stroke="#6cb21f" stroke-width="2.5"/></svg>Glen does not have any financial agreements with any individual speakers he recommends. He offers the service, as it only takes a few minutes of his time, to help promote other professional speakers and ultimately keep the very best out there in the industry.</li>
    <li><svg width="14" height="12" viewBox="0 0 14 12"><path d="M1 6 L5 10 L13 1" fill="none" stroke="#6cb21f" stroke-width="2.5"/></svg>Please understand that while Glen tries to respond quickly, due to his own speaking and travel commitments it may take up to 24 hours.</li>
  </ul>
</section>

<div class="contact-row row-2">
  <a class="cta">Quick Online Contact Form</a>
  <span class="item"><svg width="16" height="12" viewBox="0 0 16 12"><rect x=".5" y=".5" width="15" height="11" fill="none" stroke="#6cb21f"/><path d="M1 1 L8 7 L15 1" fill="none" stroke="#6cb21f"/></svg>suggestions@podiumtalentgroup.com.au</span>
  <span class="item phone"><svg width="12" height="14" viewBox="0 0 12 14"><path d="M2 1 L5 1 L5 4 L3.5 5 Q5 9 8 10.5 L9 9 L12 9 L12 12 Q6 14 1 5 Z" fill="#6cb21f"/></svg>1300 555 482</span>
</div>

<footer class="footer">© 2015, Podium Talent Group. All Rights Reserved</footer>
</body>
</html>
```